New Design Real Estate Platform - Products

We need a new PowerPoint presentation for our real estate platform products B2B area. The colors should be in the company logo. New graphics are also welcome. Some information or images (placeholders) are still missing. It should be a modern design that is clear.

Requirements
Must have
• graphics for facts & figure, new graphics in general

```html
<!DOCTYPE html>
<html lang="de">
<head>
<meta charset="utf-8">
<title>Baufeld Portal AG – Produkte B2B</title>
<link href="https://fonts.googleapis.com/css2?family=Open+Sans:wght@400;600;700;800&display=swap" rel="stylesheet">
<style>
:root{
  --lime:#8cc63f;
  --lime-strong:#7dbb2a;
  --lime-dark:#4f8f1c;
  --lime-light:#d6f0ad;
  --lime-pale:#eaf7d8;
  --ink:#2e2e2e;
  --grey:#6b6b6b;
  --grey-light:#e6e6e6;
  --paper:#ffffff;
  --gold:#e0a800;
}
*{box-sizing:border-box;margin:0;padding:0}
html,body{width:1200px;height:1200px;overflow:hidden;background:var(--paper)}
body{font-family:"Open Sans",Arial,sans-serif;color:var(--ink)}
.deck{position:absolute;left:76px;top:43px;display:grid;grid-template-columns:repeat(4,208px);grid-auto-rows:117px;column-gap:74.5px;row-gap:26.5px}
.slide{position:relative;overflow:hidden;background:var(--paper);box-shadow:0 2px 6px rgba(0,0,0,.22)}
.abs{position:absolute}
.t{position:absolute;left:0;right:0;top:6px;text-align:center;font-size:7.4px;line-height:9px;font-weight:700}
.tl{position:absolute;left:12px;top:6px;font-size:7.4px;line-height:9px;font-weight:700}
.st{position:absolute;left:10px;right:10px;top:16.5px;text-align:center;font-size:2.8px;color:var(--grey);line-height:1.25}
.p{font-size:2.6px;line-height:1.35;color:var(--grey)}
.b{font-weight:700;color:var(--ink)}
.mark{position:absolute;top:6px;right:9px;width:8px;height:8px;border:1.3px solid var(--lime);border-radius:50%}
.foot{position:absolute;left:14px;bottom:3px;font-size:1.8px;color:#9a9a9a}
.ph{position:absolute}
.ph-house{background:linear-gradient(160deg,#b9c7a8,#7d8f72 55%,#c9d3bd)}
.ph-room{background:linear-gradient(150deg,#e8e2d6,#b8ad9c 60%,#d9d2c4)}
.ph-person{background:radial-gradient(circle at 50% 40%,#d9c2ae,#a98f7a 70%);border-radius:50%;border:1.5px solid #fff}
.ph-device{background:#1e1e1e;border-radius:4px}
.ph-screen{background:linear-gradient(180deg,#f2f2f2,#cfd8c4)}
.green{background:var(--lime)}
.light{background:var(--lime-light)}
.pale{background:var(--lime-pale)}
.brand{font-weight:700;font-size:3px;color:var(--lime-dark)}
.chip{position:absolute;color:#fff;background:var(--lime);font-size:2.4px;font-weight:700;text-align:center;line-height:5px}
.dot{position:absolute;border-radius:50%;background:var(--lime)}
table{border-collapse:collapse;width:100%}
td,th{font-size:2.2px;padding:0.8px 1.5px;text-align:center}
.toc{font-size:3.2px;line-height:1.55;color:var(--ink)}
.toc b{color:var(--lime);margin-right:2px}
</style>
</head>
<body>
<main class="deck">

<!-- 1 cover green -->
<section class="slide">
  <div class="ph ph-house" style="inset:0" role="img" aria-label="Foto einer modernen Terrasse mit Garten"></div>
  <div class="abs" style="inset:0;background:rgba(140,198,63,.82)"></div>
  <div class="abs" style="left:22px;top:38px;font-size:15px;font-weight:800;color:#fff">Baufeld</div>
  <div class="abs" style="left:110px;top:40px;color:#fff;font-size:6.6px;font-weight:700;line-height:1.3">Der Match-Maker im<br>Neubau-Bereich</div>
  <div class="abs" style="left:110px;top:64px;color:#fff;font-size:4.4px;font-weight:700;line-height:1.3">Ihr Angebot &amp; unsere<br>Nachfrage!</div>
  <div class="foot" style="color:#eef">© 2024 Baufeld Portal AG</div>
</section>

<!-- 2 cover dark -->
<section class="slide">
  <div class="ph ph-room" style="inset:0" role="img" aria-label="Foto einer Neubau-Loggia mit Seeblick"></div>
  <div class="abs" style="left:10px;top:21px;width:188px;height:88px;background:rgba(40,40,40,.82)"></div>
  <div class="abs" style="left:22px;top:52px;font-size:13px;font-weight:800;color:var(--lime)">Baufeld</div>
  <div class="abs" style="left:100px;top:38px;color:var(--lime);font-size:5.8px;font-weight:700;line-height:1.3">Baufeld Portal AG<br>Der Match-Maker im<br>Neubau-Bereich</div>
  <div class="abs" style="left:100px;top:67px;color:var(--lime);font-size:3.6px;line-height:1.3">Ihr Angebot &amp; unsere<br>Nachfrage!</div>
  <div class="abs brand" style="left:100px;top:88px;color:#fff">hausfeld.ch &nbsp; PRIMOHAUS</div>
  <div class="foot" style="color:#ccc">© 2024 Baufeld Portal AG</div>
</section>

<!-- 3 cover light -->
<section class="slide">
  <div class="ph ph-room" style="inset:0" role="img" aria-label="Foto einer Neubau-Loggia mit Seeblick"></div>
  <div class="abs light" style="left:10px;top:21px;width:188px;height:88px"></div>
  <div class="abs" style="left:22px;top:52px;font-size:13px;font-weight:800;color:#2e2e2e">Baufeld</div>
  <div class="abs" style="left:100px;top:38px;font-size:5.8px;font-weight:700;line-height:1.3">Baufeld Portal AG<br>Der Match-Maker im<br>Neubau-Bereich</div>
  <div class="abs" style="left:100px;top:67px;font-size:3.6px;line-height:1.3;color:var(--grey)">Ihr Angebot &amp; unsere<br>Nachfrage!</div>
  <div class="abs brand" style="left:100px;top:88px">hausfeld.ch &nbsp; PRIMOHAUS</div>
  <div class="foot">© 2024 Baufeld Portal AG</div>
</section>

<!-- 4 TOC -->
<section class="slide">
  <div class="abs light" style="left:10px;top:15px;width:78px;height:100px"></div>
  <div class="abs" style="left:15px;top:26px;font-size:5.2px;font-weight:700;line-height:1.25">Baufeld Portal AG<br>Presentation</div>
  <div class="abs p" style="left:15px;top:45px">TABLE OF CONTENTS</div>
  <div class="mark"></div>
  <div class="abs toc" style="left:96px;top:22px">
    <b>01</b>Opportunity<br><b>02</b>Property Overview<br><b>03</b>Market Overview<br><b>04</b>Business Plan<br><b>05</b>Investment Structure<br><b>06</b>Investment Structure<br><b>07</b>Partners Overview<br><b>08</b>Appendix
  </div>
  <div class="foot">© 2024 Baufeld Portal AG</div>
</section>

<!-- 5 Welcome -->
<section class="slide">
  <div class="abs light" style="left:10px;top:16px;width:80px;height:99px"></div>
  <div class="ph ph-person" style="left:33px;top:32px;width:34px;height:34px" role="img" aria-label="Porträtfoto Co-CEO"></div>
  <div class="abs" style="left:10px;width:80px;top:70px;text-align:center;font-size:3.6px;font-weight:700">Lukas Brenner</div>
  <div class="abs p" style="left:10px;width:80px;top:76px;text-align:center;color:var(--lime-dark)">Co-CEO B2B</div>
  <div class="abs p" style="left:10px;width:80px;top:85px;text-align:center">info@baufeld-portal.ch<br>+41 (0) 79 000 00 00</div>
  <div class="mark"></div>
  <div class="abs" style="right:16px;top:24px;font-size:6.4px;font-weight:700">Welcome message</div>
  <div class="abs" style="right:16px;top:42px;font-size:4.2px;font-weight:700;text-align:right;line-height:1.2">Write Your<br>Headline Here</div>
  <div class="abs p" style="left:110px;right:16px;top:68px;text-align:right">Lorem ipsum is a short text used for layout work. It shows how body copy fills a column of this size in the final design.</div>
  <div class="foot">© 2024 Baufeld Portal AG</div>
</section>

<!-- 6 Facts & Figures -->
<section class="slide">
  <div class="t">Facts &amp; Figures</div>
  <div class="st">Nischenportal spezialisiert auf Neubauten</div>
  <div class="mark"></div>
  <div class="abs p" style="left:14px;top:28px;width:90px">• Zahlende Abonnenten sind effektiv auf der Suche nach Wohneigentum.<br>• Verlinkung der Projektwebsite im Inserat.<br>• Wir sammeln die Interessenten für Sie und geben Ihnen die Kontaktdaten weiter.<br>• Interessenten werden laufend informiert, so stellen wir sicher dass die Kunden zufrieden sind.</div>
  <div class="dot" style="left:107px;top:28px;width:22px;height:22px;display:flex;align-items:center;justify-content:center;color:#fff;font-size:6px">2.0</div>
  <div class="dot" style="left:107px;top:52px;width:22px;height:22px;background:#444;display:flex;align-items:center;justify-content:center;color:#fff;font-size:5px">+4000</div>
  <div class="dot" style="left:107px;top:76px;width:22px;height:22px;background:var(--lime-light);display:flex;align-items:center;justify-content:center;color:#fff;font-size:5px">+4000</div>
  <div class="abs p" style="left:134px;top:34px">Unique-Besucher p.a. auf<br>unseren beiden Portalen</div>
  <div class="abs p" style="left:134px;top:59px">Zahlende Abonnenten mit<br>Suchprofilen</div>
  <div class="abs p" style="left:134px;top:83px">Zahlen, Zahlen<br>Zahlen, Zahlen</div>
  <div class="foot">© 2024 Baufeld Portal AG</div>
</section>

<!-- 7 Unsere Plattform -->
<section class="slide">
  <div class="t">Unsere Plattform</div>
  <div class="mark"></div>
  <div class="abs light" style="left:0;right:0;top:16px;height:92px"></div>
  <div class="abs" style="left:14px;top:23px;width:80px;height:80px;background:#fff;border-radius:3px"></div>
  <div class="abs brand" style="left:60px;top:34px">hausfeld.ch<br>PRIMOHAUS</div>
  <div class="abs p b" style="left:22px;top:66px">hauswahl<br>wohnraum24<br>nestfinder</div>
  <div class="abs" style="left:55px;top:30px;width:.4px;height:65px;background:#ccc"></div>
  <div class="abs p" style="left:104px;top:24px;width:92px;color:#444">Mit uns inserieren Sie Ihre Neubauprojekte exklusiv und kostenlos auf dem führenden Nischenportal der Schweiz. Dank dem Suchabo für Interessenten erhalten Sie qualifizierte Anfragen und schaffen Effizienz im Vermarktungsprozess. Unsere Plattform gliedert sich in zwei Bereiche: einen geschlossenen Bereich für Abonnenten und einen öffentlichen Bereich.</div>
  <div class="foot">© 2024 Baufeld Portal AG</div>
</section>

<!-- 8 Unsere Plattform 2 -->
<section class="slide">
  <div class="abs light" style="left:0;top:0;width:78px;height:117px"></div>
  <div class="abs" style="left:17px;top:50px;font-size:6.6px;font-weight:700;line-height:1.2">Unsere<br>Plattform</div>
  <div class="mark"></div>
  <div class="abs" style="left:84px;top:16px;width:114px;height:90px;background:var(--gold);border-radius:3px"></div>
  <div class="ph ph-house" style="left:88px;top:20px;width:52px;height:27px" role="img" aria-label="Foto einer Baustelle"></div>
  <div class="ph ph-room" style="left:143px;top:20px;width:52px;height:27px" role="img" aria-label="Foto eines Neubauprojekts"></div>
  <div class="abs green" style="left:88px;top:50px;width:52px;height:53px"></div>
  <div class="abs green" style="left:143px;top:50px;width:52px;height:53px"></div>
  <div class="abs" style="left:88px;width:52px;top:53px;text-align:center;font-size:2.8px;color:#fff;line-height:1.4"><b>Vorvermarktung</b><br>Kostenloses Inserieren<br>Sichtbar nur für zahlende Abonnenten<br>Qualifizierte Anfragen<br>Evaluierung des Marktes</div>
  <div class="abs" style="left:143px;width:52px;top:53px;text-align:center;font-size:2.8px;color:#fff;line-height:1.4"><b>Öffentlicher Bereich</b><br>Projekt sichtbar für alle Suchenden<br>Kostenpflichtig, wenn das Projekt nicht bei uns ist</div>
  <div class="foot">© 2024 Baufeld Portal AG</div>
</section>

<!-- 9 Premium-Partnerschaft -->
<section class="slide">
  <div class="t">Premium-Partnerschaft</div>
  <div class="mark"></div>
  <div class="abs brand" style="left:0;right:0;top:18px;text-align:center">hausfeld.ch &nbsp; PRIMOHAUS</div>
  <svg class="abs" style="left:0;top:0" width="208" height="117" viewBox="0 0 208 117">
    <path d="M104 25v7M28 32h152M28 32v6M66 32v6M104 32v6M142 32v6M180 32v6" stroke="#c9a86a" stroke-width=".5" fill="none"/>
    <g fill="#fff" stroke="#8cc63f" stroke-width="1">
      <circle cx="28" cy="46" r="7"/><circle cx="66" cy="46" r="7"/><circle cx="104" cy="46" r="7"/><circle cx="142" cy="46" r="7"/><circle cx="180" cy="46" r="7"/>
    </g>
    <g stroke="#8cc63f" stroke-width=".8" fill="none">
      <path d="M63 44h6M63 46h6M63 48h6"/><rect x="101" y="43" width="6" height="5"/><rect x="139" y="43" width="6" height="4"/><circle cx="180" cy="46" r="2"/><path d="M24 46l3 2 5-4"/>
    </g>
  </svg>
  <div class="abs" style="left:0;right:0;top:56px;display:flex;justify-content:space-around;padding:0 6px;font-size:3px;font-weight:700"><span>"Vereinbarung"</span><span>"Geben"</span><span>"Nehmen"</span><span>"Inserieren"</span><span>"Produkte"</span></div>
  <div class="abs p" style="left:6px;right:6px;top:61px;display:flex;justify-content:space-around;text-align:center;font-size:2.2px"><span style="width:34px">Wir schliessen eine gemeinsame Partnerschaft</span><span style="width:34px">Sie inserieren neue Projekte immer mind. 4 Wochen</span><span style="width:34px">Sie erhalten kostenlos qualifizierte Anfragen</span><span style="width:34px">Vermarkten Sie Ihr Projekt effizient</span><span style="width:34px">Sie möchten gerne weitere Werbemassnahmen</span></div>
  <div class="abs light" style="left:0;right:0;top:93px;height:15px"></div>
  <div class="abs" style="left:10px;right:10px;top:95px;font-size:2.6px;font-weight:700;font-style:italic;text-align:center">Bei offiziellem Vermarktungsstart schalten Sie Ihr Projekt kostenlos im öffentlichen Bereich frei. Profitieren Sie von über 1.5 Millionen Besuchern im Jahr.</div>
  <div class="foot">© 2024 Baufeld Portal AG</div>
</section>

<!-- 10 Produkt-Übersicht -->
<section class="slide">
  <div class="t">Produkt-Übersicht</div>
  <div class="mark"></div>
  <div class="abs" style="left:11px;right:11px;top:21px">
    <table>
      <tr style="background:var(--lime);color:#fff"><th style="text-align:left">Produkte</th><th>Preis</th><th>01 Mt</th><th>Preis</th><th>03 Mt</th><th>Preis</th><th>06 Mt</th><th>Preis</th><th>12 Mt</th></tr>
      <tr><td style="text-align:left">Premiumpartnerschaft</td><td>–</td><td>–</td><td>–</td><td>–</td><td>–</td><td>–</td><td>–</td><td>–</td></tr>
      <tr style="background:var(--lime-light)"><td style="text-align:left">Projekt Insertion</td><td></td><td></td><td>99.-</td><td>x</td><td>79.-</td><td>x</td><td>59.-</td><td>x</td></tr>
      <tr><td style="text-align:left">Exklusives Listing</td><td></td><td></td><td>249.-</td><td>x</td><td>199.-</td><td>x</td><td>179.-</td><td>x</td></tr>
      <tr style="background:var(--lime-light)"><td style="text-align:left">Projektshow</td><td>1490.-</td><td>x</td><td>990.-</td><td>x</td><td>890.-</td><td>x</td><td>790.-</td><td>x</td></tr>
      <tr><td style="text-align:left">Bannerwerbung</td><td>2990.-</td><td>x</td><td>1990.-</td><td>x</td><td>1890.-</td><td>x</td><td>1790.-</td><td>x</td></tr>
    </table>
    <table style="margin-top:9px">
      <tr style="background:var(--lime-dark);color:#fff"><th style="text-align:left">Produkte</th><th>Einmalig</th><th>3er Paket</th><th>Individuell</th><th>Mindestpreis</th></tr>
      <tr style="background:var(--lime-light)"><td style="text-align:left">Newsletter</td><td>850.-</td><td>750.- / pro NL</td><td></td><td></td></tr>
      <tr><td style="text-align:left">Exklusiver Newsletter</td><td></td><td></td><td>x</td><td>2000.-</td></tr>
    </table>
  </div>
  <div class="foot">© 2024 Baufeld Portal AG</div>
</section>

<!-- 11 Premium Listing -->
<section class="slide">
  <div class="t">Premium Listing</div>
  <div class="st">Zusätzliche qualifizierte Kontakte – Vorreihung vor allen Gratis Projekten</div>
  <div class="mark"></div>
  <div class="abs light" style="left:0;right:0;top:24px;height:86px"></div>
  <div class="ph ph-screen" style="left:10px;top:27px;width:130px;height:78px;border:.6px solid #ccc" role="img" aria-label="Screenshot der Suchergebnisse mit Projektfotos"></div>
  <div class="abs p b" style="left:147px;top:30px;width:52px">Sichern Sie sich für Ihre Wohnprojekte die höchste Aufmerksamkeit in der für Sie relevanten Zielgruppe.</div>
  <div class="abs p" style="left:147px;top:60px;width:52px">Erhöhen Sie Ihre Markenbekanntheit durch Ihr exklusives Logo in der Ergebnisliste.</div>
  <div class="abs p" style="left:147px;top:82px;width:52px">Steigern Sie bis zu <b style="background:#fff200">4-mal die Anzahl</b> der Ansichten für Ihre Projektes.</div>
  <div class="foot">© 2024 Baufeld Portal AG</div>
</section>

<!-- 12 Projekt-Show -->
<section class="slide">
  <div class="t">Projekt-Show:</div>
  <div class="st">Marken- und Imagestärkung auf der Startseite</div>
  <div class="mark"></div>
  <div class="abs light" style="left:0;right:0;top:24px;height:86px"></div>
  <div class="abs p" style="left:10px;width:64px;top:28px;text-align:right"><b>Die prominenteste Platzierung auf der Startseite generiert über <span style="background:#fff200">65'000 Page-Views</span> pro Monat</b><br><br>Direkte Verlinkung zu Ihrer Projekt- oder Unternehmenswebsite.<br><br><b>Sehr hohe Wiedererkennung dank Mindestlaufzeiten</b><br><br>Max. 5 Plätze werden gleichzeitig vergeben.</div>
  <div class="ph ph-device" style="left:80px;top:27px;width:120px;height:78px" role="img" aria-label="Laptop mit Startseite des Portals"></div>
  <div class="ph ph-screen" style="left:84px;top:30px;width:112px;height:70px"></div>
  <div class="foot">© 2024 Baufeld Portal AG</div>
</section>

<!-- 13 Banner-Werbung -->
<section class="slide">
  <div class="t">Banner-Werbung</div>
  <div class="st">Marken- und Imagestärkung auf allen Kauf-Ergebnislisten</div>
  <div class="mark"></div>
  <div class="abs light" style="left:0;right:0;top:24px;height:86px"></div>
  <div class="ph ph-device" style="left:6px;top:24px;width:108px;height:95px" role="img" aria-label="Tablet mit Ergebnisliste und Werbebanner"></div>
  <div class="ph ph-screen" style="left:11px;top:29px;width:98px;height:90px"></div>
  <div class="abs p b" style="left:126px;top:37px;width:74px">Bis zu <span style="background:#fff200">50'000 monatliche Einblendungen</span> und Sichtkontakte in allen Ergebnislisten zur Suche von Kaufprojekten und Wohneinheiten.</div>
  <div class="abs p" style="left:126px;top:74px;width:74px">Es werden max. 3 Plätze gleichzeitig vergeben. Ein monatlicher Austausch Ihrer Werbebotschaft ist möglich.</div>
  <div class="foot" style="color:#ddd">© 2024 Baufeld Portal AG</div>
</section>

<!-- 14 Newsletter -->
<section class="slide">
  <div class="t">Newsletter</div>
  <div class="st">Projekt- und Unternehmensvorstellung bei allen registrierten Interessenten von Baufeld</div>
  <div class="mark"></div>
  <div class="abs p" style="left:10px;width:72px;top:36px;text-align:right"><b>Über <span style="background:#fff200">35'000</span> registrierte</b> Interessenten erhalten monatlich einen relevanten Newsletter rund um das Thema Neubau.<br><br><b>Wir vergeben 5 Projektplätze</b> pro Newsletter zur Projekt- und/oder Unternehmensvorstellung.<br><br><b>Stärken Sie Ihre Marken- und Projektpräsenz</b> bei der für Sie relevanten Zielgruppe.</div>
  <div class="ph ph-screen" style="left:100px;top:30px;width:50px;height:80px;border:.6px solid #ccc" role="img" aria-label="Newsletter-Ansicht mit Projektfotos"></div>
  <div class="ph ph-screen" style="left:155px;top:30px;width:40px;height:80px;border:.6px solid #ccc" role="img" aria-label="Newsletter-Ansicht mit Projektfotos"></div>
  <div class="foot">© 2024 Baufeld Portal AG</div>
</section>

<!-- 15 Newsletter Premium -->
<section class="slide">
  <div class="t">Newsletter Premium</div>
  <div class="st">Exklusiver Newsletter an die <span style="background:#fff200">zahlenden</span> Suchabonnenten</div>
  <div class="mark"></div>
  <div class="abs light" style="left:0;right:0;top:24px;height:86px"></div>
  <div class="ph ph-screen" style="left:12px;top:28px;width:50px;height:82px;border:.6px solid #ccc" role="img" aria-label="Premium-Newsletter mit Hausfoto"></div>
  <div class="ph ph-screen" style="left:66px;top:26px;width:36px;height:82px;border:.6px solid #ccc" role="img" aria-label="Premium-Newsletter Detailseite"></div>
  <div class="abs p" style="left:110px;top:34px;width:88px;color:#333">Entwicklung, Gestaltung und Versand Ihres personalisierten Newsletters.<br><br><b>Exklusive Versendung an unsere Suchabonnenten</b> mit den von Ihnen vorgegebenen Suchkriterien.<br><br>Direkte Ansprache Ihrer Zielgruppe <b>ohne Streuverluste.</b><br><br>Zusätzliche Visits von qualifizierten Interessenten auf Ihre Projektwebseite.</div>
  <div class="foot">© 2024 Baufeld Portal AG</div>
</section>

<!-- 16 Referenzen -->
<section class="slide">
  <div class="t">Ausgewählte Referenzen</div>
  <div class="mark"></div>
  <div class="abs light" style="left:104px;right:0;top:20px;bottom:0"></div>
  <div class="abs" style="left:10px;width:88px;top:36px;text-align:center;font-size:3.4px;font-weight:700">Von Anfang an mit dabei!</div>
  <div class="abs p" style="left:12px;width:84px;top:44px;text-align:center;font-style:italic">Die beiden Portale treffen zu 100% auf unsere Zielgruppe und werden optimal und erfolgreich auf den Plattformen platziert. Wir sind fast seit Beginn mit dabei und sehr zufrieden.<br><br><b>Jonas Fehr</b><br>CEO<br>Seeblick Wohnbau AG</div>
  <div class="abs" style="left:110px;width:92px;top:33px;text-align:center;font-size:3.4px;font-weight:700">Vielzahl an qualifizierten Interessenten</div>
  <div class="abs p" style="left:114px;width:84px;top:44px;text-align:center;font-style:italic;color:#444">Unser Verkaufsteam der Talgrund Immobilien AG durfte durch die Plattform eine Vielzahl an qualifizierten Interessenten erreichen. Ein grosser Vorteil für unsere Arbeit.<br><br><b>Reto Amsler</b><br>CEO und Leiter Vermarktung<br>Talgrund Immobilien AG</div>
  <div class="foot">© 2024 Baufeld Portal AG</div>
</section>

<!-- 17 Partner -->
<section class="slide">
  <div class="t">Ein Auszug unserer Premium-Partner</div>
  <div class="mark"></div>
  <div class="abs light" style="left:0;right:0;top:18px;bottom:0"></div>
  <div class="abs" style="left:14px;right:14px;top:24px;display:grid;grid-template-columns:repeat(4,1fr);grid-auto-rows:14px;gap:5px 8px">
    <span style="background:#b23a3a;opacity:.55;border-radius:1px"></span><span style="background:#8a6a4a;opacity:.6;border-radius:1px"></span><span style="background:#777;opacity:.4;border-radius:1px"></span><span style="background:#4a6a8a;opacity:.55;border-radius:1px"></span>
    <span style="background:#555;opacity:.45;border-radius:1px"></span><span style="background:#3a6ab2;opacity:.55;border-radius:1px"></span><span style="background:#2a7ab2;opacity:.55;border-radius:1px;grid-column:span 2"></span>
    <span style="background:#333;opacity:.5;border-radius:1px"></span><span style="background:#999;opacity:.5;border-radius:1px"></span><span style="background:#444;opacity:.5;border-radius:1px"></span><span style="background:#2a5a9a;opacity:.55;border-radius:1px"></span>
    <span style="background:#1a4a9a;opacity:.6;border-radius:1px"></span><span style="background:#777;opacity:.45;border-radius:1px"></span><span style="background:#555;opacity:.45;border-radius:1px"></span><span style="background:#2a4a9a;opacity:.6;border-radius:1px"></span>
    <span style="background:#222;opacity:.5;border-radius:1px"></span><span style="background:#444;opacity:.55;border-radius:1px"></span><span style="background:#a33;opacity:.5;border-radius:1px"></span><span style="background:#2a6ab2;opacity:.55;border-radius:1px"></span>
  </div>
  <div class="foot">© 2024 Baufeld Portal AG</div>
</section>

<!-- 18 Kontakt -->
<section class="slide">
  <div class="tl" style="left:15px">Kontakt</div>
  <div class="ph ph-house" style="left:126px;top:0;width:82px;height:117px" role="img" aria-label="Foto einer Seelandschaft mit Bergen"></div>
  <div class="abs light" style="left:11px;top:15px;width:145px;height:96px"></div>
  <div class="abs brand" style="left:33px;top:21px">hausfeld.ch</div>
  <div class="abs brand" style="left:92px;top:21px">PRIMOHAUS</div>
  <div class="ph ph-person" style="left:30px;top:30px;width:34px;height:34px" role="img" aria-label="Porträtfoto Co-CEO B2B"></div>
  <div class="ph ph-person" style="left:92px;top:30px;width:34px;height:34px" role="img" aria-label="Porträtfoto Co-CEO B2C"></div>
  <div class="abs" style="left:18px;width:58px;top:67px;text-align:center;font-size:3.4px;font-weight:700">Lukas Brenner</div>
  <div class="abs p" style="left:18px;width:58px;top:72px;text-align:center;color:var(--lime-dark)">Co-CEO B2B<br><br><span style="color:var(--grey)">info@baufeld-portal.ch<br>+41 (0) 79 000 00 00</span></div>
  <div class="abs" style="left:80px;width:58px;top:67px;text-align:center;font-size:3.4px;font-weight:700">Nora Keller</div>
  <div class="abs p" style="left:80px;width:58px;top:72px;text-align:center;color:var(--lime-dark)">Co-CEO B2C<br><br><span style="color:var(--grey)">Baufeld Portal AG<br>Musterweg 12<br>6000 Luzern</span></div>
  <div class="foot">© 2024 Baufeld Portal AG</div>
</section>

<!-- 19 Break -->
<section class="slide">
  <div class="ph" style="inset:0;background:linear-gradient(160deg,#9a9a9a,#5e5e5e 60%,#8a8a8a)" role="img" aria-label="Graustufenfoto eines Wohnraums"></div>
  <div class="abs" style="left:20px;top:50px;font-size:15px;font-weight:800;color:var(--lime)">Baufeld</div>
  <div class="abs" style="left:104px;top:52px;font-size:7.6px;font-weight:700;color:#fff">Break Section</div>
  <div class="abs brand" style="left:104px;top:66px;color:#fff">hausfeld.ch &nbsp; PRIMOHAUS</div>
  <div class="foot" style="color:#ccc">© 2024 Baufeld Portal AG</div>
</section>

<!-- 20 Business Plan 4 -->
<section class="slide">
  <div class="tl">Business Plan</div>
  <div class="abs p" style="left:12px;top:17px">Commodo consequat. Duis aute irure dolor in reprehenderit in voluptate velit esse</div>
  <div class="mark"></div>
  <div class="dot" style="left:26px;top:33px;width:18px;height:18px"></div>
  <div class="dot" style="left:112px;top:33px;width:18px;height:18px"></div>
  <div class="dot" style="left:26px;top:70px;width:18px;height:18px"></div>
  <div class="dot" style="left:112px;top:70px;width:18px;height:18px"></div>
  <svg class="abs" style="left:0;top:0" width="208" height="117"><g fill="#fff"><path d="M30 43l5-5 5 5v4h-10z"/><path d="M116 47v-6h3v-3h4v9z"/><path d="M30 84v-7h3v7zm4 0v-9h3v9zm4 0v-6h2v6z"/><path d="M116 80l5-5 5 5v4h-10z"/></g></svg>
  <div class="abs p" style="left:51px;top:36px"><b>Exterior Renovation:</b><br>Improve Curb Appeal &amp;<br>Amenity Package</div>
  <div class="abs p" style="left:137px;top:36px"><b>Exterior Renovation:</b><br>Improve Curb Appeal &amp;<br>Amenity Package</div>
  <div class="abs p" style="left:51px;top:73px"><b>Exterior Renovation:</b><br>Improve Curb Appeal &amp;<br>Amenity Package</div>
  <div class="abs p" style="left:137px;top:73px"><b>Exterior Renovation:</b><br>Improve Curb Appeal &amp;<br>Amenity Package</div>
  <div class="foot">© 2024 Baufeld Portal AG</div>
</section>

<!-- 21 Business Plan 6 -->
<section class="slide">
  <div class="tl">Business Plan</div>
  <div class="abs p" style="left:12px;top:17px">Commodo consequat. Duis aute irure dolor in reprehenderit in voluptate velit esse</div>
  <div class="mark"></div>
  <div class="dot" style="left:20px;top:34px;width:13px;height:13px"></div>
  <div class="dot" style="left:20px;top:57px;width:13px;height:13px"></div>
  <div class="dot" style="left:20px;top:80px;width:13px;height:13px"></div>
  <div class="dot" style="left:118px;top:34px;width:13px;height:13px"></div>
  <div class="dot" style="left:118px;top:57px;width:13px;height:13px"></div>
  <div class="dot" style="left:118px;top:80px;width:13px;height:13px"></div>
  <div class="abs p" style="left:41px;top:35px"><b>Exterior Renovation:</b><br>Improve Curb Appeal &amp;<br>Amenity Package</div>
  <div class="abs p" style="left:41px;top:58px"><b>Exterior Renovation:</b><br>Improve Curb Appeal &amp;<br>Amenity Package</div>
  <div class="abs p" style="left:41px;top:81px"><b>Exterior Renovation:</b><br>Improve Curb Appeal &amp;<br>Amenity Package</div>
  <div class="abs p" style="left:139px;top:35px"><b>Exterior Renovation:</b><br>Improve Curb Appeal &amp;<br>Amenity Package</div>
  <div class="abs p" style="left:139px;top:58px"><b>Exterior Renovation:</b><br>Improve Curb Appeal &amp;<br>Amenity Package</div>
  <div class="abs p" style="left:139px;top:81px"><b>Exterior Renovation:</b><br>Improve Curb Appeal &amp;<br>Amenity Package</div>
  <div class="foot">© 2024 Baufeld Portal AG</div>
</section>

<!-- 22 Mockup Device -->
<section class="slide">
  <div class="t">Mockup Device</div>
  <div class="st">Commodo consequat. Duis aute irure dolor in reprehenderit in voluptate velit esse</div>
  <div class="mark"></div>
  <div class="abs light" style="left:0;right:0;top:54px;height:56px"></div>
  <div class="ph ph-device" style="left:20px;top:24px;width:36px;height:88px" role="img" aria-label="Smartphone mit Newsletter-Ansicht"></div>
  <div class="ph ph-screen" style="left:22px;top:27px;width:32px;height:82px"></div>
  <div class="dot" style="left:49px;top:34px;width:5px;height:5px"></div>
  <div class="dot" style="left:49px;top:57px;width:5px;height:5px"></div>
  <div class="dot" style="left:49px;top:77px;width:5px;height:5px"></div>
  <div class="abs p b" style="left:72px;top:34px;color:var(--lime-dark)">Feature One</div>
  <div class="abs p b" style="left:72px;top:57px;color:var(--lime-dark)">Feature Two</div>
  <div class="abs p b" style="left:72px;top:77px;color:var(--lime-dark)">Feature Three</div>
  <div class="abs" style="left:115px;top:41px;font-size:4.2px;font-weight:700;line-height:1.2">Write Your<br>Headline Here</div>
  <div class="abs p" style="left:115px;top:58px;width:82px">Lorem ipsum is a short text used for layout work. It shows how body copy fills a column of this size and how the lines break in the final design.</div>
  <div class="foot">© 2024 Baufeld Portal AG</div>
</section>

<!-- 23 Mockup Device 2 -->
<section class="slide">
  <div class="t">Mockup Device</div>
  <div class="abs p" style="left:62px;top:18px">Commodo consequat. Duis aute irure dolor in</div>
  <div class="mark"></div>
  <div class="abs light" style="left:0;right:0;top:54px;height:56px"></div>
  <div class="ph ph-device" style="left:15px;top:16px;width:18px;height:56px" role="img" aria-label="Smartphone mit Projektansicht"></div>
  <div class="ph ph-screen" style="left:16.5px;top:18px;width:15px;height:52px"></div>
  <div class="ph ph-device" style="left:56px;top:29px;width:36px;height:80px" role="img" aria-label="Smartphone mit Newsletter-Ansicht"></div>
  <div class="ph ph-screen" style="left:58px;top:32px;width:32px;height:74px"></div>
  <div class="abs" style="left:115px;top:36px;font-size:4.2px;font-weight:700;line-height:1.2">Write Your<br>Headline Here</div>
  <div class="abs p" style="left:115px;top:52px;width:82px">Lorem ipsum is a short text used for layout work. It shows how body copy fills a column of this size and how the lines break in the final design.</div>
  <div class="foot">© 2024 Baufeld Portal AG</div>
</section>

<!-- 24 Infografik -->
<section class="slide">
  <div class="tl">Creative infografhic</div>
  <div class="abs p" style="left:12px;top:18px">YOUR SUBTITLE HERE</div>
  <div class="mark"></div>
  <div class="abs p" style="left:12px;top:36px;width:78px;text-align:justify">Quickly leverage other's distributed internal or organic sources rather than empowered materials. Conveniently leverage existing client-centric solutions with transparent ROI.<br><br>Quickly leverage other's distributed internal or organic sources rather than empowered materials. Conveniently leverage existing solutions.</div>
  <svg class="abs" style="left:104px;top:26px" width="100" height="88" viewBox="0 0 100 88">
    <circle cx="50" cy="20" r="15" fill="#e7eaef"/>
    <circle cx="74" cy="40" r="15" fill="#e0a800"/>
    <circle cx="66" cy="66" r="15" fill="#a8d96a"/>
    <circle cx="34" cy="66" r="15" fill="#6fb52b"/>
    <circle cx="26" cy="40" r="15" fill="#3b3b3b"/>
    <circle cx="50" cy="45" r="13" fill="#fff"/>
    <g font-family="Open Sans,sans-serif" font-size="5" fill="#fff" text-anchor="middle"><text x="50" y="22">02</text><text x="74" y="42">03</text><text x="66" y="68">04</text><text x="34" y="68">05</text><text x="26" y="42">01</text></g>
  </svg>
  <div class="foot">© 2024 Baufeld Portal AG</div>
</section>

<!-- 25 Road Map -->
<section class="slide">
  <div class="t">Road Map</div>
  <div class="st">Commodo consequat. Duis aute irure dolor in reprehenderit in voluptate velit esse</div>
  <div class="mark"></div>
  <div class="chip" style="left:10px;top:24px;width:44px">May 20XX</div>
  <div class="chip" style="left:58px;top:24px;width:44px">Jun 20XX</div>
  <div class="chip" style="left:106px;top:24px;width:44px;background:var(--lime-light);color:#444">Jul 20XX</div>
  <div class="chip" style="left:154px;top:24px;width:44px">Aug 20XX</div>
  <div class="abs light" style="left:106px;top:30px;width:44px;height:80px"></div>
  <div class="abs p" style="left:12px;top:33px;width:40px"><b>Your Title</b><br><br>Lorem ipsum dolor sit amet, consectetur adipiscing elit, sed do eiusmod tempor incididunt ut labore et dolore magna aliqua.</div>
  <div class="abs p" style="left:60px;top:33px;width:40px"><b>Your Title</b><br><br>Lorem ipsum is a short text used in layout and graphic design work.</div>
  <div class="abs p" style="left:108px;top:33px;width:40px"><b>Your Title</b><br><br>Lorem ipsum dolor sit amet, consectetur adipiscing elit, sed do eiusmod tempor incididunt ut labore et dolore magna aliqua. Ut enim ad minim veniam.</div>
  <div class="abs p" style="left:156px;top:33px;width:40px"><b>Your Title</b><br><br>Lorem ipsum is a short text used in layout and graphic design work.</div>
  <div class="foot">© 2024 Baufeld Portal AG</div>
</section>

<!-- 26 Our History -->
<section class="slide">
  <div class="t">Our History</div>
  <div class="mark"></div>
  <div class="abs green" style="left:40px;right:0;top:60px;height:5px"></div>
  <div class="chip" style="left:44px;top:60px;width:30px">17/7/20XX</div>
  <div class="chip" style="left:80px;top:60px;width:30px">12/5/20XX</div>
  <div class="chip" style="left:120px;top:60px;width:30px">8/3/20XX</div>
  <div class="chip" style="left:160px;top:60px;width:30px">4/9/20XX</div>
  <div class="dot" style="left:58px;top:36px;width:12px;height:12px;background:none;border:1.2px solid var(--lime)"></div>
  <div class="dot" style="left:170px;top:82px;width:12px;height:12px;background:none;border:1.2px solid var(--lime)"></div>
  <div class="abs p" style="left:78px;top:30px;width:46px;text-align:right"><b>Investor Agreement</b><br>Lorem ipsum, or lipsum a dummy text used in graphic or web designs.</div>
  <div class="abs p" style="left:146px;top:30px;width:46px;text-align:right"><b>BigExpo Contest Winner</b><br>Lorem ipsum, or lipsum a dummy text used in graphic or web designs.</div>
  <div class="abs p" style="left:40px;top:72px;width:44px;text-align:right"><b>Start Date</b><br>Lorem ipsum, or lipsum a dummy text used in graphic or web designs.</div>
  <div class="abs p" style="left:112px;top:72px;width:44px;text-align:right"><b>Milestone</b><br>Lorem ipsum, or lipsum a dummy text used in graphic or web designs.</div>
  <div class="foot">© 2024 Baufeld Portal AG</div>
</section>

<!-- 27 Our History 2 -->
<section class="slide">
  <div class="t">Our History</div>
  <div class="mark"></div>
  <div class="abs green" style="left:0;width:170px;top:60px;height:5px"></div>
  <div class="chip" style="left:4px;top:60px;width:30px">3/2/20XX</div>
  <div class="chip" style="left:56px;top:60px;width:30px">17/7/20XX</div>
  <div class="chip" style="left:94px;top:60px;width:30px">12/5/20XX</div>
  <div class="chip" style="left:134px;top:60px;width:30px">8/3/20XX</div>
  <div class="dot" style="left:64px;top:36px;width:12px;height:12px;background:none;border:1.2px solid var(--lime)"></div>
  <div class="abs p" style="left:10px;top:30px;width:46px;text-align:right"><b>Milestone</b><br>Lorem ipsum, or lipsum a dummy text used in graphic or web designs.</div>
  <div class="abs p" style="left:84px;top:30px;width:46px;text-align:right"><b>Milestone</b><br>Lorem ipsum, or lipsum a dummy text used in graphic or web designs.</div>
  <div class="abs p" style="left:48px;top:72px;width:44px;text-align:right"><b>First Product</b><br>Lorem ipsum, or lipsum a dummy text used in graphic or web designs.</div>
  <div class="abs p" style="left:120px;top:72px;width:44px;text-align:right"><b>Nowadays</b><br>Lorem ipsum, or lipsum a dummy text used in graphic or web designs.</div>
  <div class="foot">© 2024 Baufeld Portal AG</div>
</section>

<!-- 28 Costs -->
<section class="slide">
  <div class="t">Costs</div>
  <div class="st">Commodo consequat. Duis aute irure dolor in reprehenderit in voluptate velit esse cillum dolore eu fugiat nulla pariatur.</div>
  <div class="mark"></div>
  <div class="abs" style="left:14px;right:14px;top:28px">
    <table style="font-size:2.2px">
      <tr style="background:var(--lime-light)"><td style="text-align:left;padding:1.8px 2px">Graphic Design Services</td><td style="text-align:right">1000</td></tr>
      <tr><td style="text-align:left;padding:1.8px 2px">3 Year Hosting Plan</td><td style="text-align:right">600</td></tr>
      <tr style="background:var(--lime-light)"><td style="text-align:left;padding:1.8px 2px">Development</td><td style="text-align:right">2600</td></tr>
      <tr><td style="text-align:left;padding:1.8px 2px">Marketing</td><td style="text-align:right">3000</td></tr>
      <tr style="background:var(--lime-light)"><td style="text-align:left;padding:1.8px 2px">SEO</td><td style="text-align:right">1200</td></tr>
      <tr><td style="text-align:left;padding:1.8px 2px">Internet Advertising</td><td style="text-align:right">3000</td></tr>
      <tr style="background:var(--lime-light)"><td style="text-align:left;padding:1.8px 2px">Additional Landing Pages</td><td style="text-align:right">800</td></tr>
      <tr style="background:var(--lime)"><td></td><td style="text-align:right;font-weight:700;padding:1.8px 2px">Total Required Costs $ 11 500</td></tr>
    </table>
  </div>
  <div class="foot">© 2024 Baufeld Portal AG</div>
</section>

<!-- 29 Milestone Plan -->
<section class="slide">
  <div class="t">Milestone Plan</div>
  <div class="st">Commodo consequat. Duis aute irure dolor in reprehenderit in voluptate velit esse cillum dolore eu fugiat nulla pariatur.</div>
  <div class="mark"></div>
  <div class="abs" style="left:10px;right:10px;top:26px">
    <table>
      <tr style="background:var(--lime);color:#fff"><th>Stages</th><th>Initial Planning</th><th>Current Planning</th><th>Deadline</th></tr>
      <tr><td>Project Start</td><td>01.10.20XX</td><td>6.7.20XX</td><td style="background:var(--lime-light)">12.12.20XX</td></tr>
      <tr><td>Preparation</td><td>01.10.20XX</td><td>6.7.20XX</td><td style="background:var(--lime-light)">12.12.20XX</td></tr>
      <tr><td>Details Agreement</td><td>01.10.20XX</td><td>6.7.20XX</td><td style="background:var(--lime-light)">12.12.20XX</td></tr>
      <tr><td>Design</td><td>01.10.20XX</td><td>6.7.20XX</td><td style="background:var(--lime-light)">12.12.20XX</td></tr>
      <tr><td>Production</td><td>01.10.20XX</td><td>6.7.20XX</td><td style="background:var(--lime-light)">12.12.20XX</td></tr>
      <tr><td>Project Launch</td><td>01.10.20XX</td><td>6.7.20XX</td><td style="background:var(--lime-light)">12.12.20XX</td></tr>
      <tr><td>Online Marketing</td><td>01.10.20XX</td><td>6.7.20XX</td><td style="background:var(--lime-light)">12.12.20XX</td></tr>
      <tr><td>SEO</td><td>01.10.20XX</td><td>6.7.20XX</td><td style="background:var(--lime-light)">12.12.20XX</td></tr>
      <tr><td>Project closure report</td><td>01.10.20XX</td><td>6.7.20XX</td><td style="background:var(--lime-light)">12.12.20XX</td></tr>
    </table>
  </div>
  <div class="foot">© 2024 Baufeld Portal AG</div>
</section>

<!-- 30 Project Stages gantt -->
<section class="slide">
  <div class="t">Project Stages</div>
  <div class="st">Commodo consequat. Duis aute irure dolor in reprehenderit in voluptate velit esse cillum dolore eu fugiat nulla pariatur.</div>
  <div class="mark"></div>
  <div class="abs light" style="left:10px;right:10px;top:26px;height:5px;display:flex;justify-content:space-around;font-size:2.3px;font-weight:700;line-height:5px"><span>Strategy</span><span>Preparation</span><span>Design</span><span>Develop &amp; Test</span><span>Training</span><span>Support</span><span>Close</span></div>
  <svg class="abs" style="left:0;top:0" width="208" height="117">
    <g fill="#8cc63f">
      <path d="M10 33h120l3 2.5-3 2.5H10z"/><path d="M10 45h55l3 2.5-3 2.5H10z"/><path d="M10 57h185l3 2.5-3 2.5H10z"/><path d="M70 69h70l3 2.5-3 2.5H70z"/><path d="M120 81h75l3 2.5-3 2.5h-75z"/>
    </g>
    <g font-family="Open Sans,sans-serif" font-size="3" fill="#fff" text-anchor="middle"><text x="70" y="37">Management Phase</text><text x="27" y="49">Planning</text><text x="102" y="61">Control</text><text x="105" y="73">Team Management</text><text x="157" y="85">Integration</text></g>
  </svg>
  <div class="abs light" style="left:10px;right:10px;top:100px;height:5px;display:flex;justify-content:space-between;font-size:2.2px;font-weight:700;line-height:5px;padding:0 2px"><span>0/0/20XX</span><span>0/0/20XX</span><span>0/0/20XX</span><span>0/0/20XX</span><span>0/0/20XX</span><span>0/0/20XX</span><span>0/0/20XX</span></div>
  <div class="foot">© 2024 Baufeld Portal AG</div>
</section>

<!-- 31 Project Stages timeline -->
<section class="slide">
  <div class="t">Project Stages</div>
  <div class="st">Commodo consequat. Duis aute irure dolor in reprehenderit in voluptate velit esse cillum dolore eu fugiat nulla pariatur.</div>
  <div class="mark"></div>
  <div class="abs p" style="left:14px;top:30px;width:40px;text-align:center"><b>Milestone One</b><br>Lorem ipsum, or lipsum a dummy text used in graphic or web designs.</div>
  <div class="abs p" style="left:84px;top:30px;width:40px;text-align:center"><b>Milestone Two</b><br>Lorem ipsum, or lipsum a dummy text used in graphic or web designs.</div>
  <div class="abs p" style="left:154px;top:30px;width:40px;text-align:center"><b>Milestone Three</b><br>Lorem ipsum, or lipsum a dummy text used in graphic or web designs.</div>
  <div class="abs green" style="left:10px;right:0;top:61px;height:7px;display:flex;justify-content:space-around;color:#fff;font-size:2.4px;font-weight:700;line-height:7px"><span>1/12/20XX</span><span>1/18/20XX</span><span>1/25/20XX</span><span>1/30/20XX</span><span>2/1/20XX</span></div>
  <div class="abs pale" style="left:20px;top:74px;width:46px;height:5px;font-size:2.2px;text-align:center;line-height:5px">The stage of data collection</div>
  <div class="abs pale" style="left:70px;top:86px;width:52px;height:5px;font-size:2.2px;text-align:center;line-height:5px">Marketing Research</div>
  <div class="abs pale" style="left:106px;top:97px;width:40px;height:5px;font-size:2.2px;text-align:center;line-height:5px">Pre-Launch Testing</div>
  <div class="abs pale" style="left:150px;top:97px;width:40px;height:5px;font-size:2.2px;text-align:center;line-height:5px">Advertising Campaign</div>
  <div class="foot">© 2024 Baufeld Portal AG</div>
</section>

<!-- 32 Project Stages timeline 2 -->
<section class="slide">
  <div class="t">Project Stages</div>
  <div class="st">Commodo consequat. Duis aute irure dolor in reprehenderit in voluptate velit esse cillum dolore eu fugiat nulla pariatur.</div>
  <div class="mark"></div>
  <div class="abs p" style="left:14px;top:30px;width:40px;text-align:center"><b>Milestone Four</b><br>Lorem ipsum, or lipsum a dummy text used in graphic or web designs.</div>
  <div class="abs p" style="left:84px;top:30px;width:40px;text-align:center"><b>Milestone Five</b><br>Lorem ipsum, or lipsum a dummy text used in graphic or web designs.</div>
  <div class="abs p" style="left:154px;top:30px;width:40px;text-align:center"><b>Milestone Six</b><br>Lorem ipsum, or lipsum a dummy text used in graphic or web designs.</div>
  <div class="abs green" style="left:0;right:10px;top:61px;height:7px;display:flex;justify-content:space-around;color:#fff;font-size:2.4px;font-weight:700;line-height:7px"><span>2/4/20XX</span><span>2/10/20XX</span><span>2/26/20XX</span><span>3/5/20XX</span><span>3/15/20XX</span></div>
  <div class="abs pale" style="left:20px;top:74px;width:46px;height:5px;font-size:2.2px;text-align:center;line-height:5px">Promo Campaign</div>
  <div class="abs pale" style="left:60px;top:86px;width:40px;height:5px;font-size:2.2px;text-align:center;line-height:5px">Product Launch</div>
  <div class="abs pale" style="left:106px;top:86px;width:40px;height:5px;font-size:2.2px;text-align:center;line-height:5px">SEO Campaign</div>
  <div class="abs pale" style="left:152px;top:86px;width:40px;height:5px;font-size:2.2px;text-align:center;line-height:5px">Service Stage</div>
  <div class="abs pale" style="left:0;top:97px;width:40px;height:5px;font-size:2.2px;text-align:center;line-height:5px">Advertising Campaign</div>
  <div class="foot">© 2024 Baufeld Portal AG</div>
</section>

</main>
</body>
</html>
```